New Webpage for High Class Expert Witness Services Company

We are looking for a minimalist design for a webpage that just has our logo and an entry form offer to connect with one of our Liaisons.
The entry form should just ask for Name, Email, Contact Info and Description of Project.

Company Name is: The Marlowe Crest Advisory Services

Number of Pages Required

1 page

```html
<!DOCTYPE html>
<html lang="en">
<head>
<meta charset="UTF-8">
<title>The Marlowe Crest Advisory Services – Connect With A Liaison</title>
<link href="https://fonts.googleapis.com/css2?family=Cinzel:wght@500;600&family=Poppins:wght@400;500;600&display=swap" rel="stylesheet">
<style>
  :root {
    --bg: #000000;
    --frame: #2a2a2c;
    --field-bg: #0e0e0f;
    --field-border: #2c2c2e;
    --card-bg: #0b0b0c;
    --card-border: #262628;
    --text: #ffffff;
    --muted: #8a8a8e;
    --rule: #3a3a3c;
    --silver-a: #c3c4c8;
    --silver-b: #e2e2e4;
    --ink: #0a0a0a;
  }
  * { box-sizing: border-box; margin: 0; padding: 0; }
  html, body { width: 1164px; height: 1200px; overflow: hidden; background: var(--bg); }
  body { position: relative; font-family: 'Poppins', sans-serif; color: var(--text); }

  .contact-frame {
    position: absolute; left: 137px; top: 101px; width: 890px; height: 634px;
    border: 1px solid var(--frame);
  }
  .brand {
    position: absolute; left: 361px; top: 64px; width: 442px; height: 76px;
    background: var(--bg);
    display: flex; align-items: center; justify-content: center; gap: 14px;
  }
  .brand-mark {
    width: 40px; height: 40px;
    background: linear-gradient(135deg, var(--silver-a), var(--silver-b));
  }
  .brand-name { font-family: 'Cinzel', serif; font-weight: 500; color: #d6d6d8; line-height: 1; }
  .brand-name .line-main { display: block; font-size: 29px; letter-spacing: 0.5px; }
  .brand-name .line-sub { display: block; font-size: 13.5px; letter-spacing: 4.6px; margin-top: 6px; }

  .section-title {
    position: absolute; left: 0; width: 1164px; text-align: center;
    font-family: 'Cinzel', serif; font-weight: 600; font-size: 30px; letter-spacing: 0.5px; line-height: 1;
  }
  .title-connect { top: 173px; }
  .title-touch { top: 801px; }

  .intro {
    position: absolute; left: 0; top: 210px; width: 1164px; text-align: center;
    font-size: 12.4px; line-height: 19px;
  }

  .divider { position: absolute; display: flex; align-items: center; justify-content: center; gap: 14px; }
  .divider .rule { height: 1px; background: var(--rule); }
  .divider .mark {
    width: 14px; height: 14px;
    background: linear-gradient(135deg, var(--silver-a), var(--silver-b));
  }
  .divider-connect { left: 433px; top: 268px; width: 302px; }
  .divider-connect .rule { width: 130px; }
  .divider-touch { left: 487px; top: 847px; width: 188px; }
  .divider-touch .rule { width: 76px; }

  .liaison-form {
    position: absolute; left: 283px; top: 309px; width: 598px;
    display: grid; grid-template-columns: 291px 291px; column-gap: 16px; row-gap: 18px;
  }
  .field-group.full { grid-column: 1 / 3; }
  .field-label { display: block; font-size: 11.6px; line-height: 14px; margin-bottom: 8px; padding-left: 1px; }
  .field {
    position: relative; height: 52px;
    background: var(--field-bg); border: 1px solid var(--field-border);
    display: flex; align-items: center; padding-left: 36px;
    font-size: 11.4px; color: var(--muted);
  }
  .field.textarea { height: 105px; align-items: flex-start; padding-top: 18px; }
  .field svg { position: absolute; left: 12px; top: 50%; transform: translateY(-50%); width: 14px; height: 14px; }
  .field.textarea svg { top: 26px; }
  .submit-button {
    grid-column: 1 / 3; margin-top: 3px; height: 52px; border: none;
    background: linear-gradient(90deg, var(--silver-a), var(--silver-b));
    font-family: 'Poppins', sans-serif; font-weight: 600; font-size: 12px; color: var(--ink);
    letter-spacing: 0.2px;
  }

  .info-cards { position: absolute; left: 137px; top: 916px; width: 890px; display: flex; gap: 35px; }
  .info-card { position: relative; width: 273px; height: 173px; }
  .info-card .panel {
    position: absolute; left: 0; top: 26px; width: 273px; height: 147px;
    background: var(--card-bg); border: 1px solid var(--card-border);
  }
  .info-card .icon-box {
    position: absolute; left: 106px; top: 0; width: 62px; height: 62px;
    background: linear-gradient(135deg, var(--silver-a), var(--silver-b));
    display: flex; align-items: center; justify-content: center;
  }
  .info-card h3 {
    position: absolute; left: 0; top: 84px; width: 273px; text-align: center;
    font-weight: 500; font-size: 17px; line-height: 22px;
  }
  .info-card p {
    position: absolute; left: 0; top: 111px; width: 273px; text-align: center;
    font-size: 12.8px; line-height: 20px;
  }

  .footer-rule { position: absolute; left: 137px; top: 1146px; width: 890px; height: 1px; background: var(--card-border); }
  .copyright { position: absolute; left: 0; top: 1165px; width: 1164px; text-align: center; font-size: 12.6px; line-height: 18px; }
</style>
</head>
<body>
  <div class="contact-frame"></div>

  <header class="brand">
    <div class="brand-mark"></div>
    <div class="brand-name">
      <span class="line-main">MARLOWE CREST</span>
      <span class="line-sub">ADVISORY SERVICES</span>
    </div>
  </header>

  <h1 class="section-title title-connect">CONNECT WITH A LIAISON</h1>
  <p class="intro">High-Class Expert Witness Support. Share Your Project Details And A<br>Dedicated Liaison Will Reach You Within 24 Hours.</p>
  <div class="divider divider-connect"><span class="rule"></span><span class="mark"></span><span class="rule"></span></div>

  <form class="liaison-form">
    <div class="field-group">
      <label class="field-label">First Name *</label>
      <div class="field">
        <svg viewBox="0 0 16 16" fill="none" stroke="#8a8a8e" stroke-width="1.1"><circle cx="8" cy="5" r="3"/><path d="M2.5 15c0-3.2 2.5-5.2 5.5-5.2s5.5 2 5.5 5.2"/></svg>
        First Name
      </div>
    </div>
    <div class="field-group">
      <label class="field-label">Last Name *</label>
      <div class="field">
        <svg viewBox="0 0 16 16" fill="none" stroke="#8a8a8e" stroke-width="1.1"><circle cx="8" cy="5" r="3"/><path d="M2.5 15c0-3.2 2.5-5.2 5.5-5.2s5.5 2 5.5 5.2"/></svg>
        Last Name
      </div>
    </div>
    <div class="field-group">
      <label class="field-label">Email Address *</label>
      <div class="field">
        <svg viewBox="0 0 16 16" fill="none" stroke="#8a8a8e" stroke-width="1.1"><path d="M1.5 6.5 8 2l6.5 4.5V14h-13z"/><path d="M1.5 6.5 8 10.5l6.5-4"/></svg>
        Your Email
      </div>
    </div>
    <div class="field-group">
      <label class="field-label">Contact Info (Phone / Direct Line) *</label>
      <div class="field">
        <svg viewBox="0 0 16 16" fill="none" stroke="#8a8a8e" stroke-width="1.1"><path d="M3 1.5h2.5l1.2 3-1.6 1.2a8 8 0 0 0 5.2 5.2l1.2-1.6 3 1.2V13a1.5 1.5 0 0 1-1.5 1.5A12 12 0 0 1 1.5 3 1.5 1.5 0 0 1 3 1.5z"/><path d="M11 2v3M13.5 2v3"/></svg>
        Phone
      </div>
    </div>
    <div class="field-group full">
      <label class="field-label">Description Of Project *</label>
      <div class="field textarea">
        <svg viewBox="0 0 16 16" fill="none" stroke="#8a8a8e" stroke-width="1.1"><path d="M8 2c3.6 0 6.5 2.4 6.5 5.5S11.6 13 8 13c-.9 0-1.8-.1-2.6-.4L2 14l1-2.8C2 10.2 1.5 8.9 1.5 7.5 1.5 4.4 4.4 2 8 2z"/><path d="M5 6.5h6M5 8.8h4"/></svg>
        Provide Key Case Details, Litigation Area, Required Expertise, Deadlines...
      </div>
    </div>
    <button class="submit-button" type="button">SUBMIT NOW</button>
  </form>

  <h2 class="section-title title-touch">GET IN TOUCH</h2>
  <div class="divider divider-touch"><span class="rule"></span><span class="mark"></span><span class="rule"></span></div>

  <section class="info-cards">
    <div class="info-card">
      <div class="panel"></div>
      <div class="icon-box">
        <svg width="28" height="36" viewBox="0 0 28 36"><path d="M14 1C6.8 1 1 6.6 1 13.6 1 23 14 35 14 35s13-12 13-21.4C27 6.6 21.2 1 14 1z" fill="#0a0a0a"/><circle cx="14" cy="13.5" r="5" fill="none" stroke="#d0d0d3" stroke-width="2.6"/></svg>
      </div>
      <h3>Contact Details</h3>
      <p>Suite 410, Building 3, Floor 12, 20418<br>North Harbor Crest Drive, Suite 12C</p>
    </div>
    <div class="info-card">
      <div class="panel"></div>
      <div class="icon-box">
        <svg width="32" height="26" viewBox="0 0 32 26"><rect x="1" y="1" width="30" height="24" rx="3" fill="#0a0a0a"/><path d="M4 5l12 10L28 5M4 22l9-8M28 22l-9-8" fill="none" stroke="#d0d0d3" stroke-width="1.8"/></svg>
      </div>
      <h3>Email Address</h3>
      <p>Info@Marlowecrest.Com</p>
    </div>
    <div class="info-card">
      <div class="panel"></div>
      <div class="icon-box">
        <svg width="32" height="32" viewBox="0 0 32 32"><path d="M6 3h5l2.5 6-3.2 2.4a16 16 0 0 0 10.3 10.3l2.4-3.2 6 2.5v5a3 3 0 0 1-3 3C14.3 29 3 17.7 3 6a3 3 0 0 1 3-3z" fill="#0a0a0a"/><path d="M19 8a6 6 0 0 1 5 5M19.5 3.5a10.5 10.5 0 0 1 9 9" fill="none" stroke="#0a0a0a" stroke-width="2" stroke-linecap="round"/></svg>
      </div>
      <h3>Phone Number</h3>
      <p>-61 (555) 014 2290</p>
    </div>
  </section>

  <div class="footer-rule"></div>
  <p class="copyright">2026 The Marlowe Crest Advisory Services All Right</p>
</body>
</html>
```